Juniper Hollow Meditation

Logo picture and I want it to say

yoga. meditation. sound healing

small sweet classes

Juniperhollow-meditation.com

2417 West Larkspur Ave Suite D
Santa Barbara ca 94872

```html
<!DOCTYPE html>
<html lang="en">
<head>
<meta charset="utf-8">
<title>Juniper Hollow Meditation – Flyer</title>
<link href="https://fonts.googleapis.com/css2?family=Anton&family=Poppins:wght@400;600&display=swap" rel="stylesheet">
<style>
  :root {
    --backdrop: #4a4240;
    --paper: #f6f6f6;
    --purple-light: #a487c3;
    --purple-deep: #74459b;
    --purple-line: #9b7cc0;
    --charcoal: #3a3a3a;
    --ink: #333333;
    --white: #ffffff;
  }
  html, body {
    margin: 0;
    padding: 0;
    width: 1200px;
    height: 2371px;
    overflow: hidden;
    background: var(--backdrop);
  }
  .flyer {
    position: absolute;
    left: 50px;
    top: 474px;
    width: 1100px;
    height: 1423px;
    box-shadow: 0 20px 40px rgba(0,0,0,0.35);
  }
  .flyer svg { display: block; width: 100%; height: 100%; }
  .headline { font-family: "Anton", "Oswald", sans-serif; fill: var(--white); }
  .tagline { font-family: "Poppins", sans-serif; font-weight: 400; fill: var(--white); letter-spacing: 1px; }
  .brand-name { font-family: "Poppins", sans-serif; font-weight: 400; fill: var(--ink); }
  .web-name { font-family: "Poppins", sans-serif; font-weight: 600; fill: var(--purple-line); }
  .web-tld { font-family: "Poppins", sans-serif; font-weight: 400; fill: var(--ink); }
  .address { font-family: "Poppins", sans-serif; font-weight: 400; fill: var(--ink); }
</style>
</head>
<body>
<div class="flyer">
  <svg viewBox="0 0 1056 1366" xmlns="http://www.w3.org/2000/svg">
    <defs>
      <linearGradient id="purpleFill" x1="0" y1="0" x2="0" y2="1">
        <stop offset="0" stop-color="var(--purple-light)"/>
        <stop offset="1" stop-color="var(--purple-deep)"/>
      </linearGradient>
      <linearGradient id="portraitTone" x1="0" y1="0" x2="0" y2="1">
        <stop offset="0" stop-color="#fafafa"/>
        <stop offset="0.55" stop-color="#f1efed"/>
        <stop offset="0.8" stop-color="#d9d6d4"/>
        <stop offset="1" stop-color="#b8b5b3"/>
      </linearGradient>
      <linearGradient id="matTone" x1="0" y1="0" x2="1" y2="1">
        <stop offset="0" stop-color="#e8eef6"/>
        <stop offset="0.5" stop-color="#b9cbe3"/>
        <stop offset="1" stop-color="#2b3f8f"/>
      </linearGradient>
      <linearGradient id="pillFill" x1="0" y1="0" x2="1" y2="0">
        <stop offset="0" stop-color="#0d0d0d"/>
        <stop offset="0.5" stop-color="#3a3a3a"/>
        <stop offset="1" stop-color="#0d0d0d"/>
      </linearGradient>
    </defs>

    <!-- paper -->
    <rect class="paper" width="1056" height="1366" fill="var(--paper)"/>

    <!-- main purple field -->
    <path class="purple-field" d="M0,520 C90,410 250,360 350,360 C460,362 530,440 600,500 C760,590 960,520 1056,340 L1056,1366 L0,1366 Z" fill="url(#purpleFill)"/>

    <!-- portrait photo area -->
    <path class="portrait-photo" role="img" aria-label="Photo of a woman meditating cross-legged in a white t-shirt and grey trousers"
          d="M0,92 C150,32 380,92 500,278 C570,390 620,500 620,590 C620,700 540,760 380,762 L80,762 C30,762 0,730 0,690 Z"
          fill="url(#portraitTone)"/>
    <path class="top-arc" d="M0,84 C150,24 380,84 500,270" fill="none" stroke="var(--purple-line)" stroke-width="10"/>

    <!-- yoga mat photo area -->
    <path class="mat-photo" role="img" aria-label="Photo of a hand rolling a blue yoga mat by a bright window"
          d="M600,500 C760,590 960,520 1056,350 L1056,760 C900,820 720,800 640,640 Z" fill="url(#matTone)"/>
    <path class="mat-top-band" d="M596,494 C760,586 960,516 1056,344" fill="none" stroke="var(--purple-line)" stroke-width="12"/>
    <path class="mat-bottom-band" d="M604,560 C680,780 880,830 1056,760" fill="none" stroke="var(--charcoal)" stroke-width="14"/>

    <!-- brand mark -->
    <g class="brand-badge">
      <circle cx="807" cy="245" r="185" fill="none" stroke="var(--charcoal)" stroke-width="5"/>
      <text class="brand-name" x="807" y="238" text-anchor="middle" font-size="38">Juniper Hollow</text>
      <text class="brand-name" x="807" y="284" text-anchor="middle" font-size="38">Meditation</text>
    </g>

    <!-- headline -->
    <text class="headline" x="528" y="918" text-anchor="middle" font-size="100" textLength="678" lengthAdjust="spacingAndGlyphs">YOGA. MEDITATION.</text>
    <text class="headline" x="528" y="1015" text-anchor="middle" font-size="100" textLength="561" lengthAdjust="spacingAndGlyphs">SOUND HEALING</text>

    <!-- tagline pill -->
    <rect class="tagline-pill" x="150" y="1040" width="756" height="66" rx="33" fill="url(#pillFill)"/>
    <text class="tagline" x="528" y="1090" text-anchor="middle" font-size="46" textLength="560" lengthAdjust="spacingAndGlyphs">SMALL SWEET CLASSES</text>

    <!-- contact arch -->
    <path class="arch-edge" d="M70,1366 C190,1222 420,1162 540,1162 C700,1162 880,1250 975,1366 Z" fill="var(--charcoal)"/>
    <path class="arch-face" d="M120,1366 C240,1224 430,1156 540,1156 C700,1158 845,1250 940,1366 Z" fill="var(--white)"/>

    <!-- globe icon -->
    <g class="web-icon" transform="translate(527,1197)" fill="none" stroke="var(--white)" stroke-width="2">
      <circle r="19" fill="var(--purple-line)" stroke="none"/>
      <circle r="11"/>
      <ellipse rx="5" ry="11"/>
      <line x1="-11" y1="0" x2="11" y2="0"/>
      <line x1="-9" y1="-6" x2="9" y2="-6"/>
      <line x1="-9" y1="6" x2="9" y2="6"/>
    </g>

    <text x="528" y="1246" text-anchor="middle" font-size="27"><tspan class="web-name">Juniperhollow-meditation</tspan><tspan class="web-tld">.com</tspan></text>
    <text class="address" x="528" y="1290" text-anchor="middle" font-size="25">2417 West Larkspur Ave Suite D</text>
    <text class="address" x="528" y="1326" text-anchor="middle" font-size="25">Santa Barbara ca 94872</text>
  </svg>
</div>
</body>
</html>
```